Stylish Business Cards Wanted

- DOUBLE SIDED Design Required -

High end, edgy cards for a corporate and personal stylist. Must include logo,
Name: Belinda Harwick
Title: Director and Stylist
telephone : +61 8 7142 5809
email: belinda@theloombriefing.example
website: theloombriefing.example
Tag: Corporate Workwear & Uniform Specialist | Personal Stylist
Would like nice icons for telephone, email, website

Target Market(s)

Businesses wanting stylish uniforms, people wanting stylish wardrobes

Industry/Entity Type

Corporate Workwear Stylist

Contact Information for Business Card

I would like black, white and gold foiling incorporated in the design - possibly a touch of the other colours on my branding guide attached Name: Belinda Harwick Title: Director and Stylist telephone : +61 8 7142 5809 email: belinda@theloombriefing.example website: theloombriefing.example Tag: Corporate Workwear & Uniform Specialist | Personal Stylist Would like nice icons for telephone, email, website

Font styles to use
Other font styles liked:
• Raleway

Colors

Designer to choose colors to be used in the design.

Requirements
Must have
• Gold foil accents

```html
<!DOCTYPE html>
<html lang="en">
<head>
<meta charset="utf-8">
<title>The Loom Briefing — Business Card</title>
<link rel="stylesheet" href="https://fonts.googleapis.com/css2?family=Raleway:wght@400;500;700&family=Dancing+Script:wght@600;700&display=swap">
<style>
  :root {
    --navy: #151b2f;
    --gold: #dbb04c;
    --gold-soft: #e6c26a;
    --white: #ffffff;
    --backdrop: #c9c9c9;
    --text-sans: "Raleway", Arial, sans-serif;
    --text-script: "Dancing Script", cursive;
  }
  * { box-sizing: border-box; margin: 0; padding: 0; }
  html, body { width: 1200px; height: 852px; overflow: hidden; }
  body { background: var(--backdrop); position: relative; font-family: var(--text-sans); }

  .card {
    position: absolute;
    width: 520px;
    height: 300px;
    border-radius: 22px;
    background: var(--navy);
    overflow: hidden;
    box-shadow: 0 10px 24px rgba(0,0,0,0.25);
  }
  .card--front { left: 60px; top: 150px; }
  .card--back { left: 620px; top: 400px; }

  .brand {
    position: absolute;
    font-family: var(--text-sans);
    font-weight: 700;
    text-align: center;
    line-height: 1.05;
    letter-spacing: 1px;
  }
  .card--front .brand {
    left: 0; right: 0; top: 102px;
    color: var(--gold);
    font-size: 40px;
  }
  .card--back .brand {
    right: 34px; top: 136px;
    color: var(--white);
    font-size: 30px;
  }

  .swoosh { position: absolute; inset: 0; width: 100%; height: 100%; }

  .tagline {
    position: absolute;
    right: 30px; top: 20px;
    text-align: right;
    font-family: var(--text-script);
    font-weight: 600;
    font-size: 15px;
    line-height: 1.15;
    color: var(--navy);
  }

  .person { position: absolute; left: 34px; top: 172px; }
  .person__name {
    font-family: var(--text-script);
    font-weight: 700;
    font-size: 27px;
    color: var(--gold);
    line-height: 1;
  }
  .person__title {
    font-size: 11px;
    color: var(--white);
    margin-top: 3px;
  }

  .contacts {
    position: absolute;
    left: 34px; top: 228px;
    list-style: none;
  }
  .contacts li {
    display: flex;
    align-items: center;
    gap: 8px;
    font-size: 11px;
    color: var(--white);
    height: 15px;
  }
  .contacts .social li { gap: 10px; }
  .icon { width: 12px; height: 12px; flex: none; }
  .icon--social { width: 30px; height: 10px; }
</style>
</head>
<body>

  <section class="card card--front" aria-label="Card front">
    <p class="brand">The Loom<br>Briefing</p>
  </section>

  <section class="card card--back" aria-label="Card back">
    <svg class="swoosh" viewBox="0 0 520 300" preserveAspectRatio="none" aria-hidden="true">
      <path d="M0,0 H520 V62 C410,70 250,100 120,150 C70,168 30,185 0,200 Z" fill="var(--gold)"/>
      <path d="M520,66 C400,78 260,108 150,150 C100,168 60,182 40,196 C90,170 200,128 300,104 C380,86 460,74 520,70 Z" fill="var(--navy)"/>
      <path d="M420,80 C330,92 220,118 130,156 C80,176 40,190 15,198 C70,176 170,136 250,114 C320,96 380,86 420,80 Z" fill="var(--navy)"/>
    </svg>

    <p class="tagline">Corporate Workwear «<br>and Uniform Specialist «<br>Personal Stylist «</p>

    <p class="brand">The Loom<br>Briefing</p>

    <div class="person">
      <p class="person__name">Belinda Harwick</p>
      <p class="person__title">Director and Stylist</p>
    </div>

    <ul class="contacts">
      <li>
        <svg class="icon" viewBox="0 0 12 12" aria-hidden="true"><rect x="1" y="1" width="10" height="10" rx="2" fill="var(--gold)"/></svg>
        /theloombriefing101
      </li>
      <li>
        <svg class="icon" viewBox="0 0 12 12" aria-hidden="true"><circle cx="6" cy="6" r="5" fill="none" stroke="var(--gold)" stroke-width="1.2"/><path d="M4,3.5 L5,3.5 L5.5,5 L4.8,5.5 C5.2,6.4 5.8,7 6.5,7.2 L7,6.5 L8.5,7 L8.5,8 C6,8.3 3.7,6 4,3.5 Z" fill="var(--gold)"/></svg>
        +61 8 7142 5809
      </li>
      <li>
        <svg class="icon" viewBox="0 0 12 12" aria-hidden="true"><rect x="1" y="2.5" width="10" height="7" fill="none" stroke="var(--gold)" stroke-width="1.2"/><path d="M1,2.5 L6,6.5 L11,2.5" fill="none" stroke="var(--gold)" stroke-width="1.2"/></svg>
        belinda@theloombriefing.example
      </li>
      <li>
        <svg class="icon" viewBox="0 0 12 12" aria-hidden="true"><circle cx="6" cy="6" r="5" fill="none" stroke="var(--gold)" stroke-width="1.2"/><ellipse cx="6" cy="6" rx="2.2" ry="5" fill="none" stroke="var(--gold)" stroke-width="1"/><path d="M1,6 H11" stroke="var(--gold)" stroke-width="1"/></svg>
        theloombriefing.example
      </li>
    </ul>
  </section>

</body>
</html>
```